Varnik Holdings — Business Card Design Brief
Overview
Design a double-sided business card for Varnik Holdings that highlights our two service arms: Varnik Communications (telecommunications) and Varnik Energy (business energy solutions). The card should feel smart and stand out when handed to clients.

Objectives
Showcase our areas of specialty clearly.
Reflect the overall Varnik / Varnik Holdings brand while acknowledging both arms.
Explore using both logos (Communications + Energy) or one unified logo, depending on the design.

Deliverables
One double-sided business card design (front + back).

Content & Copy
Front (preferred): Logo: Varnik / Varnik Holdings
Descriptor: Business Communications | Business Energy
Back:My contact details and company details
Core products: Business Mobile • Telephony • Internet • Business Energy Solutions

Brand & Visual Direction
We have a group logo currently tailored more toward telecoms, plus a separate Varnik Energy logo.
Please explore layouts that use both logos or just one, whichever works best.
Color: I wouldn't mind seeing an option using our the Blue/Purple gradient from our website (varnik-example.co.uk), but also open to non-gradient approaches and other colours..

Overall look: Smart, modern, and distinctive.
Format & Print Specs
Double-sided business card format. (Use a standard size

Must-Haves
Front: Varnik wording or Varnik Holdings wording with atleast 1 logo also on front “Business Communications | Business Energy.”

Back: Contact + company details and core products.
A design that stands out while remaining professional.

Nice-to-Have Options
A gradient version using our site’s Blue/Purple gradient.
A non-gradient version.
A dual-logo treatment versus a single-logo treatment.

Thanks
Owen

```html
<!DOCTYPE html>
<html lang="en">
<head>
<meta charset="utf-8">
<title>Varnik Business Card</title>
<link rel="stylesheet" href="https://fonts.googleapis.com/css2?family=Montserrat:wght@400;500;700;800&display=swap">
<style>
  :root {
    --bg: #e6e7ea;
    --card: #ffffff;
    --navy: #232565;
    --blue: #2f8fd6;
    --green: #3daa48;
    --lime: #c8cf1f;
    --ink: #1d1d2b;
  }
  * { box-sizing: border-box; margin: 0; padding: 0; }
  html, body { width: 1200px; height: 875px; overflow: hidden; }
  body {
    background: var(--bg);
    font-family: "Montserrat", sans-serif;
    color: var(--ink);
    display: flex;
    align-items: center;
    justify-content: center;
    gap: 40px;
  }
  .card {
    position: relative;
    width: 540px;
    height: 310px;
    background: var(--card);
    border-radius: 22px;
    overflow: hidden;
    box-shadow: 0 18px 40px rgba(0,0,0,.18);
  }

  /* Front */
  .front-brand {
    position: absolute;
    left: 0; right: 0; top: 96px;
    display: flex;
    align-items: center;
    justify-content: center;
    gap: 18px;
  }
  .brand-dot {
    width: 62px; height: 62px;
    border-radius: 50%;
    background: var(--green);
  }
  .brand-name {
    font-weight: 800;
    font-size: 66px;
    letter-spacing: 1px;
    color: var(--navy);
    line-height: 1;
  }
  .descriptor {
    position: absolute;
    left: 0; right: 0; bottom: 56px;
    display: flex;
    justify-content: center;
    align-items: center;
    gap: 12px;
    font-size: 15px;
    font-weight: 500;
    color: var(--ink);
  }
  .descriptor-sep {
    width: 2px; height: 16px;
    background: var(--lime);
  }

  /* Back */
  .back-brand {
    position: absolute;
    left: 30px; top: 112px;
    display: flex;
    align-items: center;
    gap: 10px;
  }
  .back-brand .brand-dot { width: 32px; height: 32px; background: var(--blue); }
  .back-brand .brand-name { font-size: 36px; }
  .divider {
    position: absolute;
    left: 252px; top: 40px;
    width: 1px; height: 170px;
    background: var(--navy);
  }
  .contact {
    position: absolute;
    left: 272px; top: 40px;
    width: 255px;
  }
  .contact-name { font-weight: 800; font-size: 24px; color: var(--navy); line-height: 1.1; }
  .contact-role { font-size: 12.5px; font-weight: 500; margin-top: 3px; }
  .contact-address { font-size: 12.5px; margin-top: 10px; line-height: 1.3; }
  .contact-list { list-style: none; margin-top: 10px; font-size: 12.5px; }
  .contact-list li { display: flex; align-items: center; gap: 8px; margin-bottom: 4px; }
  .contact-list svg { width: 12px; height: 12px; fill: var(--blue); flex: none; }
  .products {
    position: absolute;
    left: 0; right: 0; bottom: 34px;
    display: flex;
    justify-content: center;
    gap: 12px;
    list-style: none;
    font-size: 12px;
    font-weight: 500;
  }
  .products li { display: flex; align-items: center; gap: 6px; white-space: nowrap; }
  .products li::before {
    content: "";
    width: 6px; height: 6px;
    border-radius: 50%;
    background: var(--lime);
  }
  .band {
    position: absolute;
    left: 0; right: 0; bottom: 0;
    height: 14px;
  }
</style>
</head>
<body>

  <section class="card card-front">
    <div class="front-brand">
      <span class="brand-dot"></span>
      <span class="brand-name">VARNIK</span>
    </div>
    <p class="descriptor">
      <span>Business Communications</span>
      <span class="descriptor-sep"></span>
      <span>Business Energy</span>
    </p>
  </section>

  <section class="card card-back">
    <div class="back-brand">
      <span class="brand-dot"></span>
      <span class="brand-name">VARNIK</span>
    </div>
    <div class="divider"></div>
    <div class="contact">
      <p class="contact-name">Owen Marlow</p>
      <p class="contact-role">Business Development Manager</p>
      <p class="contact-address">48 Kestrel Park,<br>London, UK</p>
      <ul class="contact-list">
        <li>
          <svg viewBox="0 0 24 24"><path d="M6.6 10.8a15 15 0 0 0 6.6 6.6l2.2-2.2c.3-.3.7-.4 1-.2 1.1.4 2.3.6 3.6.6.6 0 1 .4 1 1V20c0 .6-.4 1-1 1A17 17 0 0 1 3 4c0-.6.4-1 1-1h3.5c.6 0 1 .4 1 1 0 1.3.2 2.5.6 3.6.1.3 0 .7-.2 1z"/></svg>
          +44 (0)1632 960 418
        </li>
        <li>
          <svg viewBox="0 0 24 24"><path d="M2 5h20v14H2zm2 2v.5l8 5 8-5V7z"/></svg>
          owen.marlow@varnik-example.co.uk
        </li>
        <li>
          <svg viewBox="0 0 24 24"><circle cx="12" cy="12" r="10"/></svg>
          www.varnik-example.co.uk
        </li>
      </ul>
    </div>
    <ul class="products">
      <li>Business Mobile</li>
      <li>Telephony</li>
      <li>Internet</li>
      <li>Business Energy Solutions</li>
    </ul>
    <svg class="band" viewBox="0 0 540 14" preserveAspectRatio="none">
      <polygon points="0,0 330,0 318,14 0,14" fill="#232565"/>
      <polygon points="330,0 540,0 540,14 318,14" fill="#2f8fd6"/>
    </svg>
  </section>

</body>
</html>
```